Business Card Design

I need a business card for a new company based in Australia called "MedLinkora".

Its a cloud program for GPs that allows them to search for the specialist they require using a simple user friendly tool.

I would like the colours to match those in the program (the colours in the logo attached).

The final design should reflect the programs clarity, ease of use and professionalism.

Target Market(s)

GPs and other Health Professionals

Industry/Entity Type

Business

Contact Information for Business Card

MedLinkora; The Whole Consultant Index; Marla Voss CEO; 0438215967; marla@medlinkora.example; www.medlinkora.example

Requirements
Must have
• Must have the logo attached; the web address and my name and phone number
Nice to have
• the slogan "The Whole Consultant Index"

```html
<!DOCTYPE html>
<html lang="en">
<head>
<meta charset="utf-8">
<title>MedLinkora – Business Card</title>
<link rel="stylesheet" href="https://fonts.googleapis.com/css2?family=Didact+Gothic&family=Source+Sans+3:wght@400;700&display=swap">
<style>
  :root {
    --brand-blue: #29b4e4;
    --brand-grey: #9d9ea1;
    --ink: #2e2e30;
    --card-white: #ffffff;
    --backdrop: #ecebe8;
  }
  * { box-sizing: border-box; margin: 0; padding: 0; }
  html, body {
    width: 1200px;
    height: 1200px;
    overflow: hidden;
    background: var(--backdrop);
  }
  .card {
    position: absolute;
    left: 150px;
    width: 900px;
    height: 550px;
    border-radius: 36px;
    overflow: hidden;
  }
  .card--front { top: 33px; background: var(--card-white); }
  .card--back  { top: 617px; background: var(--brand-blue); }

  .front-swoosh {
    position: absolute;
    inset: 0;
    width: 900px;
    height: 550px;
  }
  .holder {
    position: absolute;
    top: 38px;
    right: 52px;
    text-align: right;
    color: var(--card-white);
    font-family: "Source Sans 3", sans-serif;
  }
  .holder__name { font-weight: 700; font-size: 36px; line-height: 1.1; }
  .holder__role { font-weight: 400; font-size: 25px; line-height: 1.3; }

  .wordmark {
    font-family: "Didact Gothic", sans-serif;
    font-weight: 400;
    line-height: 1;
    letter-spacing: -0.01em;
  }
  .tagline {
    font-family: "Didact Gothic", sans-serif;
    font-weight: 400;
    line-height: 1.2;
  }
  .card--front .brand { position: absolute; left: 56px; top: 200px; }
  .card--front .wordmark { font-size: 98px; color: var(--brand-blue); }
  .card--front .tagline { font-size: 30px; color: var(--brand-grey); margin-top: 6px; padding-left: 6px; }

  .contacts {
    position: absolute;
    left: 62px;
    top: 382px;
    list-style: none;
    font-family: "Source Sans 3", sans-serif;
    font-size: 31px;
    color: var(--ink);
  }
  .contacts li { display: flex; align-items: center; gap: 14px; height: 48px; }
  .contacts svg { width: 26px; height: 26px; flex: none; }

  .card--back .brand {
    position: absolute;
    left: 0; right: 0;
    top: 150px;
    text-align: center;
    color: var(--card-white);
  }
  .card--back .wordmark { font-size: 118px; }
  .card--back .tagline { font-size: 36px; margin-top: 8px; }
  .back-web {
    position: absolute;
    left: 0; right: 0;
    top: 385px;
    text-align: center;
    color: var(--card-white);
    font-family: "Source Sans 3", sans-serif;
    font-size: 36px;
    letter-spacing: 0.14em;
  }
</style>
</head>
<body>

<section class="card card--front" aria-label="Business card front">
  <svg class="front-swoosh" viewBox="0 0 900 550" aria-hidden="true">
    <path d="M0,0 H900 V252 C660,140 330,70 0,98 Z" fill="var(--brand-grey)"/>
    <path d="M0,0 H900 V228 C660,118 330,56 0,86 Z" fill="var(--brand-blue)"/>
  </svg>

  <div class="holder">
    <p class="holder__name">Marla Voss</p>
    <p class="holder__role">CEO</p>
  </div>

  <div class="brand">
    <p class="wordmark">MedLinkora</p>
    <p class="tagline">The Whole Consultant Index</p>
  </div>

  <ul class="contacts">
    <li>
      <svg viewBox="0 0 24 24" aria-hidden="true">
        <circle cx="12" cy="12" r="11" fill="none" stroke="var(--brand-blue)" stroke-width="2"/>
        <path d="M8.5 6.5l2 2.5-1.2 1.4c.7 1.6 1.8 2.8 3.4 3.6l1.4-1.2 2.5 2-1.3 1.9c-4.2-.6-7.6-4-8.3-8.3z" fill="var(--brand-blue)"/>
      </svg>
      <span>0438215967</span>
    </li>
    <li>
      <svg viewBox="0 0 24 24" aria-hidden="true">
        <rect x="2" y="6" width="20" height="13" rx="2" fill="var(--brand-blue)"/>
        <path d="M3 7l9 7 9-7" fill="none" stroke="var(--card-white)" stroke-width="1.8"/>
      </svg>
      <span>marla@medlinkora.example</span>
    </li>
    <li>
      <svg viewBox="0 0 24 24" aria-hidden="true">
        <circle cx="12" cy="12" r="10" fill="var(--brand-blue)"/>
        <g fill="none" stroke="var(--card-white)" stroke-width="1.3">
          <ellipse cx="12" cy="12" rx="4.2" ry="10"/>
          <path d="M2 12h20M4 7h16M4 17h16M12 2v20"/>
        </g>
      </svg>
      <span>www.medlinkora.example</span>
    </li>
  </ul>
</section>

<section class="card card--back" aria-label="Business card back">
  <div class="brand">
    <p class="wordmark">MedLinkora</p>
    <p class="tagline">The Whole Consultant Index</p>
  </div>
  <p class="back-web">www.medlinkora.example</p>
</section>

</body>
</html>
```